Business Card Design for Software Development Company

I am looking for a business card design the incorporates my new logo (attached below).

Key information to include:
Name: Martin Quelbrook
Title: CEO
Email: martin@brightwellcivic.example
Phone: 555-218-9403
Website: www.brightwellcivic.example

NOTE: This design should be easy to edit so that we can order cards for different members of our team.

```html
<!DOCTYPE html>
<html lang="en">
<head>
<meta charset="utf-8">
<title>Northvane Labs – Business Card</title>
<link rel="stylesheet" href="https://fonts.googleapis.com/css2?family=Montserrat:wght@400;500;600;700&display=swap">
<style>
  :root {
    --backdrop: #333436;
    --card-white: #ffffff;
    --card-navy: #3a4259;
    --ink-navy: #353e57;
    --ink-dark: #2a2f3d;
    --ink-white: #ffffff;
  }
  * { box-sizing: border-box; margin: 0; padding: 0; }
  html, body {
    width: 1200px; height: 1059px; overflow: hidden;
    background: var(--backdrop);
    font-family: "Montserrat", sans-serif;
  }
  .canvas { position: relative; width: 1200px; height: 1059px; }
  .card {
    position: absolute; left: 255px; width: 690px; height: 392px;
    box-shadow: 0 18px 30px rgba(0,0,0,0.45);
  }
  .card--front { top: 100px; background: var(--card-white); }
  .card--back { top: 538px; background: var(--card-navy); }

  .brand-name {
    position: absolute; font-weight: 600; white-space: nowrap; letter-spacing: -0.5px;
  }
  .brand-tagline {
    position: absolute; font-weight: 700; text-transform: uppercase;
    white-space: nowrap; letter-spacing: 0.3px;
  }
  .card--front .brand-name { left: 36px; top: 170px; font-size: 34px; color: var(--ink-navy); }
  .card--front .brand-tagline { left: 207px; top: 211px; font-size: 5px; color: var(--ink-navy); }

  .divider {
    position: absolute; left: 343px; top: 109px; width: 1.5px; height: 173px;
    background: var(--ink-navy);
  }
  .contact-block { position: absolute; left: 372px; top: 110px; color: var(--ink-dark); }
  .person-name {
    font-size: 26px; font-weight: 700; color: var(--ink-navy);
    letter-spacing: 0.2px; line-height: 1.1;
  }
  .person-title { font-size: 17px; font-weight: 400; line-height: 1.2; }
  .rule { width: 17px; height: 1.5px; background: var(--ink-dark); margin: 21px 0 27px; }
  .contact-list { list-style: none; }
  .contact-list li {
    display: flex; align-items: center; gap: 8px;
    font-size: 16px; font-weight: 400; height: 26px; letter-spacing: 0.2px;
  }
  .contact-list svg { width: 13px; height: 13px; flex: none; fill: var(--ink-navy); }

  .card--back .brand-name { left: 100px; top: 140px; font-size: 70px; color: var(--ink-white); }
  .card--back .brand-tagline { right: 96px; top: 224px; font-size: 8px; color: var(--ink-white); }
</style>
</head>
<body>
<main class="canvas">
  <section class="card card--front" aria-label="Business card front">
    <div class="brand-name">Northvane Labs</div>
    <div class="brand-tagline">A division of Brightwell Civic</div>
    <div class="divider"></div>
    <div class="contact-block">
      <h1 class="person-name">MARTIN QUELBROOK</h1>
      <p class="person-title">CEO</p>
      <div class="rule"></div>
      <ul class="contact-list">
        <li>
          <svg viewBox="0 0 24 24" aria-hidden="true"><path d="M6.6 10.8a15.1 15.1 0 0 0 6.6 6.6l2.2-2.2c.3-.3.7-.4 1-.2 1.1.4 2.3.6 3.6.6.6 0 1 .4 1 1V20c0 .6-.4 1-1 1A17 17 0 0 1 3 4c0-.6.4-1 1-1h3.5c.6 0 1 .4 1 1 0 1.3.2 2.5.6 3.6.1.3 0 .7-.2 1z"/></svg>
          <span>555-218-9403</span>
        </li>
        <li>
          <svg viewBox="0 0 24 24" aria-hidden="true"><path d="M2 5h20v2l-10 6L2 7z"/><path d="M2 9.3l10 6 10-6V19H2z"/></svg>
          <span>martin@brightwellcivic.example</span>
        </li>
        <li>
          <svg viewBox="0 0 24 24" aria-hidden="true"><path d="M12 2a10 10 0 1 0 0 20 10 10 0 0 0 0-20zm6.9 6h-3a15 15 0 0 0-1.3-3.9A8 8 0 0 1 18.9 8zM12 4c.8 1.2 1.5 2.5 1.9 4h-3.8c.4-1.5 1.1-2.8 1.9-4zM4.3 14a8 8 0 0 1 0-4h3.4a16 16 0 0 0 0 4zm.8 2h3a15 15 0 0 0 1.3 3.9A8 8 0 0 1 5.1 16zm3-8h-3a8 8 0 0 1 4.3-3.9C8.8 5.3 8.4 6.6 8.1 8zM12 20c-.8-1.2-1.5-2.5-1.9-4h3.8c-.4 1.5-1.1 2.8-1.9 4zm2.3-6H9.7a14 14 0 0 1 0-4h4.6a14 14 0 0 1 0 4zm.3 5.9c.6-1.2 1-2.5 1.3-3.9h3a8 8 0 0 1-4.3 3.9zM16.3 14a16 16 0 0 0 0-4h3.4a8 8 0 0 1 0 4z"/></svg>
          <span>www.brightwellcivic.example</span>
        </li>
      </ul>
    </div>
  </section>

  <section class="card card--back" aria-label="Business card back">
    <div class="brand-name">Northvane Labs</div>
    <div class="brand-tagline">A division of Brightwell Civic</div>
  </section>
</main>
</body>
</html>
```